Business Cards for a law firm

Business cards for our law firm. Use our silhoette logo and OAK PARTNERS - check our website (www.oakpartners.example)

Contact Information for Business Card

our silhouette logo, OAK PARTNERS, 800-555-0147, Dorian Pemberton, dorian@oakpartners.example

Requirements
Must have
• our silhouette logo, OAK PARTNERS, 800-555-0147, Dorian Pemberton, dorian@oakpartners.example

```html
<!DOCTYPE html>
<html lang="en">
<head>
<meta charset="utf-8">
<title>Oak Partners — Business Cards</title>
<link href="https://fonts.googleapis.com/css2?family=Cinzel:wght@600&family=Lato:wght@400;700&display=swap" rel="stylesheet">
<style>
  :root {
    --navy: #1b3168;
    --ink: #111111;
    --paper: #ffffff;
    --backdrop: #e4e3e4;
  }
  html, body {
    margin: 0;
    padding: 0;
    width: 1200px;
    height: 1108px;
    overflow: hidden;
    background: var(--backdrop);
    font-family: "Lato", sans-serif;
  }
  .canvas {
    position: relative;
    width: 1200px;
    height: 1108px;
  }
  .card {
    position: absolute;
    left: 231px;
    width: 778px;
    height: 446px;
    box-sizing: border-box;
  }
  .card--front {
    top: 68px;
    background: var(--paper);
  }
  .card--back {
    top: 596px;
    background: var(--navy);
  }
  .brand {
    position: absolute;
    display: flex;
    align-items: center;
    font-family: "Cinzel", serif;
    font-weight: 600;
    white-space: nowrap;
  }
  .card--front .brand {
    left: 112px;
    top: 60px;
    color: var(--navy);
    font-size: 46px;
    letter-spacing: 4px;
  }
  .brand-mark {
    width: 62px;
    height: 62px;
    background: var(--navy);
    margin-right: 34px;
  }
  .holder-name {
    position: absolute;
    left: 37px;
    top: 230px;
    margin: 0;
    color: var(--navy);
    font-size: 30px;
    font-weight: 700;
  }
  .holder-title {
    position: absolute;
    left: 38px;
    top: 276px;
    margin: 0;
    color: var(--ink);
    font-size: 20px;
    font-weight: 400;
  }
  .divider {
    position: absolute;
    left: 42px;
    top: 315px;
    width: 698px;
    height: 2px;
    background: var(--ink);
  }
  .contact-list {
    position: absolute;
    left: 36px;
    top: 330px;
    margin: 0;
    padding: 0;
    list-style: none;
  }
  .contact-item {
    display: flex;
    align-items: center;
    height: 30.5px;
    font-size: 20px;
    color: var(--ink);
  }
  .contact-icon {
    width: 22px;
    height: 22px;
    margin-right: 11px;
    fill: var(--navy);
    flex: none;
  }
  .card--back .brand {
    right: 38px;
    bottom: 28px;
    color: var(--paper);
    font-size: 42px;
    letter-spacing: 4px;
  }
</style>
</head>
<body>
<main class="canvas">
  <section class="card card--front" aria-label="Business card front">
    <div class="brand"><span class="brand-mark"></span>OAK PARTNERS</div>
    <h1 class="holder-name">Dorian Pemberton</h1>
    <p class="holder-title">Managing Director</p>
    <div class="divider"></div>
    <ul class="contact-list">
      <li class="contact-item">
        <svg class="contact-icon" viewBox="0 0 24 24" aria-hidden="true"><path d="M6.6 10.8a15.1 15.1 0 0 0 6.6 6.6l2.2-2.2a1 1 0 0 1 1-.25 11.4 11.4 0 0 0 3.6.57 1 1 0 0 1 1 1V20a1 1 0 0 1-1 1A17 17 0 0 1 3 4a1 1 0 0 1 1-1h3.5a1 1 0 0 1 1 1c0 1.25.2 2.45.57 3.57a1 1 0 0 1-.25 1z"/></svg>
        800-555-0147
      </li>
      <li class="contact-item">
        <svg class="contact-icon" viewBox="0 0 24 24" aria-hidden="true"><path d="M2 5h20v2.2l-10 6-10-6z"/><path d="M2 9.5l10 6 10-6V19H2z"/></svg>
        dorian@oakpartners.example
      </li>
      <li class="contact-item">
        <svg class="contact-icon" viewBox="0 0 24 24" aria-hidden="true"><circle cx="12" cy="12" r="10" fill="none" stroke="#1b3168" stroke-width="2"/><path d="M12 2a10 10 0 0 1 0 20M2 12h20M12 2c-3 3-3 17 0 20"/></svg>
        www.oakpartners.example
      </li>
    </ul>
  </section>

  <section class="card card--back" aria-label="Business card back">
    <div class="brand">OAK PARTNERS</div>
  </section>
</main>
</body>
</html>
```